Creative, fresh business card design for Ripplecraft Facades

We need a fresh, creative business card design for Ripplecraft Facades. We are the manufacturer of Ripplecraft Facades in Australia. Wall panels are 2400 x 1200mm panels made from MDF and feature 3D patterns on the face of the panel. The colours to be used are green, silver/grey and white RGB
Red 187
Green 207
Blue 65.

An idea is to possibly use a watermark of one of our designs as a background (like on the "Grids" design on the left hand side of page 2 of our brochure).

Target Market(s)

Interior designers, architects, builders and home renovators

Industry/Entity Type

Business

Contact Information for Business Card

Details to go on the card are:
Our logo (attached),
Slogan: "Decorative panels for interiors and exteriors",
Contact name,
Position,
Mobile phone number,
Business address,
Business phone,
Business fax,
Website and
Email address.

I have attached a few images of our panels and our brochure for reference.

The colours of the business card should feature our logo colours which are: RGB
Red 187
Green 207
Blue 65

Requirements
Must have
• Very modern fonts and design. Some of the designs shown especially the "Prisms" design which is a popular design.
Nice to have
• Creative but simple design. Very contemporary.
Should not have
• Anything ornate or old fashioned.

```html
<!DOCTYPE html>
<html lang="en">
<head>
<meta charset="utf-8">
<title>Ripplecraft Facades – Business Card</title>
<link href="https://fonts.googleapis.com/css2?family=Open+Sans:wght@400;600&display=swap" rel="stylesheet">
<style>
  :root {
    --brand-green: #bbcf41;
    --green-light: #c9dc4f;
    --green-mid: #a9c03a;
    --green-deep: #7f9d2c;
    --grey: #9a9a9c;
    --grey-dark: #5e5e60;
    --white: #ffffff;
    --backdrop: #e6e6e4;
  }
  * { box-sizing: border-box; margin: 0; padding: 0; }
  html, body { width: 1200px; height: 1000px; overflow: hidden; }
  body {
    background: var(--backdrop);
    font-family: "Open Sans", sans-serif;
    display: flex; align-items: center; justify-content: center;
  }
  .card {
    width: 440px; height: 770px;
    background: var(--white);
    position: relative;
    overflow: hidden;
    box-shadow: 0 6px 24px rgba(0,0,0,.12);
  }
  .brand {
    height: 330px;
    display: flex; flex-direction: column; align-items: center; justify-content: center;
    gap: 14px;
  }
  .brand__row { display: flex; align-items: center; gap: 14px; }
  .brand__square { width: 58px; height: 58px; background: var(--brand-green); }
  .brand__name { font-size: 30px; font-weight: 600; color: var(--grey); line-height: 1.05; }
  .brand__slogan {
    font-size: 15px; letter-spacing: 3px; color: var(--grey);
    text-align: left; line-height: 1.25; width: 300px;
  }
  .web-band {
    height: 36px; background: var(--brand-green);
    color: var(--white); font-size: 13px; letter-spacing: 5px;
    display: flex; align-items: center; justify-content: center;
  }
  .person {
    height: 104px; position: relative;
    padding: 20px 0 0 62px;
    background: linear-gradient(90deg, var(--white) 55%, #eef4cc 100%);
  }
  .person__bar {
    position: absolute; left: 34px; top: 20px;
    width: 7px; height: 64px; background: var(--brand-green);
  }
  .person__name { font-size: 32px; font-weight: 600; color: var(--brand-green); line-height: 1.1; letter-spacing: .5px; }
  .person__role { font-size: 19px; color: var(--grey-dark); margin-top: 4px; }
  .contacts { height: 300px; display: flex; flex-direction: column; }
  .contact { flex: 1; display: flex; color: var(--white); font-size: 18px; }
  .contact__icon {
    width: 98px; display: flex; align-items: center; justify-content: center;
  }
  .contact__icon svg { width: 24px; height: 24px; fill: var(--white); }
  .contact__text { flex: 1; display: flex; flex-direction: column; justify-content: center; padding-left: 22px; line-height: 1.25; }
  .contact--phone   { background: var(--green-light); }
  .contact--phone .contact__icon { background: #bcd045; }
  .contact--email   { background: #bdd043; }
  .contact--email .contact__icon { background: #adc23d; }
  .contact--fax     { background: #a9c03a; }
  .contact--fax .contact__icon { background: #98b035; }
  .contact--address { background: #93ae33; }
  .contact--address .contact__icon { background: var(--green-deep); }
  .contact--address .contact__text { font-size: 16px; }
</style>
</head>
<body>
  <main class="card">
    <section class="brand">
      <div class="brand__row">
        <div class="brand__square"></div>
        <div class="brand__name">Ripplecraft<br>Facades</div>
      </div>
      <p class="brand__slogan">decorative panels for interiors &amp; landscapes</p>
    </section>

    <div class="web-band">www.ripplecraftfacades.com</div>

    <section class="person">
      <span class="person__bar"></span>
      <h1 class="person__name">DANA WHITFIELD</h1>
      <p class="person__role">Director</p>
    </section>

    <section class="contacts">
      <div class="contact contact--phone">
        <div class="contact__icon">
          <svg viewBox="0 0 24 24"><path d="M6.6 10.8a15 15 0 0 0 6.6 6.6l2.2-2.2a1 1 0 0 1 1-.25 11.4 11.4 0 0 0 3.6.57 1 1 0 0 1 1 1V20a1 1 0 0 1-1 1A17 17 0 0 1 3 4a1 1 0 0 1 1-1h3.5a1 1 0 0 1 1 1c0 1.25.2 2.45.57 3.57a1 1 0 0 1-.25 1z"/></svg>
        </div>
        <div class="contact__text"><span>+000 123 456 789</span><span>+000 123 456 789</span></div>
      </div>
      <div class="contact contact--email">
        <div class="contact__icon">
          <svg viewBox="0 0 24 24"><path d="M2 5h20v14H2z" fill="none" stroke="#fff" stroke-width="2"/><path d="M2 5l10 8 10-8" fill="none" stroke="#fff" stroke-width="2"/></svg>
        </div>
        <div class="contact__text">yourname@email.com</div>
      </div>
      <div class="contact contact--fax">
        <div class="contact__icon">
          <svg viewBox="0 0 24 24"><path d="M7 3h8l2 2v4H7z"/><rect x="3" y="10" width="18" height="9" rx="1.5"/><rect x="7" y="15" width="10" height="6" fill="#98b035"/></svg>
        </div>
        <div class="contact__text">+000 123 456 789</div>
      </div>
      <div class="contact contact--address">
        <div class="contact__icon">
          <svg viewBox="0 0 24 24"><path d="M12 2a7 7 0 0 0-7 7c0 5 7 13 7 13s7-8 7-13a7 7 0 0 0-7-7zm0 9.5A2.5 2.5 0 1 1 12 6.5a2.5 2.5 0 0 1 0 5z"/></svg>
        </div>
        <div class="contact__text">Your Street Address, NewYork 123,</div>
      </div>
    </section>
  </main>
</body>
</html>
```